Our new beauty salon requires a price list brochure

Our beauty clinic is a medical grade skin care clinic. So our salon is very clinical and professional in appearance. I would like the colours to be similar to our logo design with some nice texture or abstract shapes thrown in.
Pricelist, contact details and logo is attached
I would prefer it to be a 3 fold brochure.

Target Market(s)

Females aged 30-50

Colors
85acd3
cedeed
c4c4c4
5c5c5c
000000
ffffff
eea3c7
f9d9e8
dbdbdb

Requirements
Must have
• easy to read

```html
<!DOCTYPE html>
<html lang="en">
<head>
<meta charset="utf-8">
<title>Willow Aesthetics – Brochure Cover Panel</title>
<link rel="stylesheet" href="https://fonts.googleapis.com/css2?family=Raleway:ital,wght@0,300;1,300&display=swap">
<style>
  :root {
    --brand-blue: #85acd3;
    --paper: #ffffff;
    --ink: #4b5b6b;
    --trim: #9a9a9a;
    --shadow: rgba(60, 80, 110, 0.25);
  }
  html, body {
    margin: 0;
    padding: 0;
    width: 1200px;
    height: 2542px;
    overflow: hidden;
    background: var(--paper);
  }
  .panel {
    position: relative;
    width: 1200px;
    height: 2542px;
    font-family: "Raleway", "Helvetica Neue", Arial, sans-serif;
    font-weight: 300;
    color: var(--ink);
  }
  .panel-art {
    position: absolute;
    inset: 0;
  }
  .brand {
    position: absolute;
    left: 330px;
    top: 1380px;
    width: 760px;
    text-align: center;
    color: var(--ink);
    font-weight: 300;
  }
  .brand-name {
    display: block;
    font-size: 150px;
    line-height: 1;
    letter-spacing: 4px;
    text-transform: lowercase;
  }
  .brand-tag {
    display: block;
    margin-top: 40px;
    font-size: 30px;
    letter-spacing: 22px;
    text-transform: uppercase;
  }
  .contact {
    position: absolute;
    right: 258px;
    top: 1842px;
    text-align: right;
    font-size: 38px;
    line-height: 50px;
  }
  .contact p { margin: 0; }
  .contact-web {
    font-style: italic;
    margin-top: 0;
  }
  .contact-social {
    display: flex;
    justify-content: flex-end;
    align-items: center;
    gap: 14px;
    margin-top: 12px !important;
    line-height: 52px;
  }
  .social-mark {
    display: inline-block;
    width: 46px;
    height: 46px;
    border-radius: 8px;
    background: var(--brand-blue);
  }
</style>
</head>
<body>
<main class="panel">
  <svg class="panel-art" width="1200" height="2542" viewBox="0 0 1200 2542" xmlns="http://www.w3.org/2000/svg">
    <defs>
      <filter id="soft-lift" x="-10%" y="-10%" width="120%" height="120%">
        <feDropShadow dx="-4" dy="6" stdDeviation="6" flood-color="#3c506e" flood-opacity="0.25"/>
      </filter>
    </defs>
    <rect class="panel-field" x="35" y="45" width="1133" height="2420" fill="#85acd3"/>
    <path class="panel-cutout" role="img" aria-label="White cut-out silhouette of a woman in profile with hair in a bun"
          d="M35 1560 C 190 1230 470 1030 740 1020 C 960 1015 1080 1260 1130 1700 C 1150 1900 1160 2100 1168 2300 L1168 2465 L35 2465 Z"
          fill="#ffffff" filter="url(#soft-lift)"/>
    <rect class="trim-frame" x="35" y="45" width="1133" height="2420" fill="none" stroke="#9a9a9a" stroke-width="2"/>
    <line class="fold-line" x1="1168" y1="45" x2="1168" y2="2465" stroke="#9a9a9a" stroke-width="3" stroke-dasharray="28 14"/>
  </svg>

  <div class="brand">
    <span class="brand-name">willow</span>
    <span class="brand-tag">Aesthetics</span>
  </div>

  <address class="contact" style="font-style: normal;">
    <p>Willow Aesthetics</p>
    <p>4/28 Harbour Road</p>
    <p>Coral Bay</p>
    <p>Western Australia</p>
    <p>(08) 5550 1234</p>
    <p class="contact-web">www.willowaesthetics.example</p>
    <p class="contact-social">willow_aesthetics <span class="social-mark"></span></p>
    <p class="contact-social">willow aesthetics studio <span class="social-mark"></span></p>
  </address>
</main>
</body>
</html>
```